Flyer Design for Upcoming Baseball Clinics, Camps, and Academies

What We Need:
We are looking for a design template we can use for our upcoming sports camps, clinics, and academies. We do elite level training with youth to professional athletes and brand awareness is our number one concern right now.

Ideally this template can be used across multiple sports. Here is our premise:

Clinics (1-Day Event to attract 50+ Athletes)
Camps (2-4 Day Events looking to attract 100+)
Academies (More intimate and skill specific. lasts 6-8 weeks. 10-20 athletes)

Our plan is to do this for Baseball, Football, Basketball, and Lacrosse.

The ideal situation is to be able to use this as a template so we can just edit the document in the future.

Target Market(s)

Prep: Middle School Athletes / ELITE: High School Athletes

Industry/Entity Type

Training

Requirements
Must have
• Things to include:
• Logo, Dates, Times, Investment, Description, Benefits, our mission statement, etc. Our specific colors, specific font family (Bunken Tech Sans Wide), follow our branding deck which is attached.
• Info:
• K7T BASEBALL CLINIC
• Date: November 11th, 2017
• AGES: PREP: (5th to 8th Grade). ELITE (9th-12th Grade)
• Registration: 8:00am - 9:00 am / 11:00 am - Noon
• Times:
• PREP: 9:00am - 11:00 am
• ELITE: Noon - 2pm
• Investment: $199
• Current Members: $99
Nice to have
• It would be nice to see our mission statement tied in somehow in a unique way. Also maybe a testimonial or two from our pro athletes??
Should not have
• Fake Images: Any Image used needs to be real and give off an authentic feel of a baseball player and the culture.

```html
<!DOCTYPE html>
<html lang="en">
<head>
<meta charset="utf-8">
<title>K7T Baseball Clinic Flyer</title>
<link rel="stylesheet" href="https://fonts.googleapis.com/css2?family=Michroma&display=swap">
<style>
  :root {
    --frame: #828387;
    --slate: #3d4346;
    --teal: #1e8a9b;
    --white: #ffffff;
    --ink: #2b2f31;
    --font-wide: "Michroma", sans-serif;
  }
  * { margin: 0; padding: 0; box-sizing: border-box; }
  html, body { width: 907px; height: 1200px; overflow: hidden; }
  body { background: var(--frame); font-family: var(--font-wide); }

  .flyer {
    position: absolute; left: 39px; top: 62px;
    width: 829px; height: 1075px;
    background: var(--white); overflow: hidden;
  }

  .photo-collage { position: absolute; left: 0; top: 0; width: 829px; height: 429px; display: block; }

  .brand-mark {
    position: absolute; left: 26px; top: 38px;
    display: flex; align-items: center; gap: 8px;
    color: var(--white); font-size: 22px; letter-spacing: 1px;
  }
  .brand-mark .dot { width: 12px; height: 12px; border-radius: 50%; background: var(--white); }

  .mission { position: absolute; left: 0; top: 429px; width: 829px; height: 99px; }
  .mission svg { position: absolute; inset: 0; }
  .mission-text {
    position: absolute; inset: 0; text-align: center; color: var(--white);
  }
  .mission-label { position: absolute; top: 10px; width: 100%; font-size: 14px; font-weight: 700; letter-spacing: 1px; }
  .mission-line { position: absolute; top: 33px; width: 100%; font-size: 13.5px; }
  .mission-tagline { position: absolute; top: 55px; width: 100%; font-size: 26px; letter-spacing: 1px; }

  .statement {
    position: absolute; top: 539px; width: 100%; text-align: center;
    color: var(--ink); font-size: 14.6px; line-height: 25px; white-space: nowrap;
  }

  .program { position: absolute; top: 595px; width: 230px; margin-left: -115px; text-align: center; }
  .program-badge {
    width: 124px; height: 124px; margin: 0 auto; border-radius: 50%;
    background: var(--teal); color: var(--white);
    display: flex; align-items: center; justify-content: center;
    font-size: 15px; letter-spacing: 0.5px;
  }
  .program-badge.small { font-size: 12.5px; }
  .program-note { margin-top: 15px; color: var(--ink); font-size: 11.5px; line-height: 18px; white-space: nowrap; }
  .program.clinics { left: 136px; }
  .program.camps { left: 401px; }
  .program.academies { left: 679px; }

  .event-bar {
    position: absolute; left: 0; top: 805px; width: 829px; height: 59px;
    background: var(--teal); color: var(--white); text-align: center;
  }
  .event-title { position: absolute; top: 8px; width: 100%; font-size: 17px; font-weight: 700; letter-spacing: 1px; }
  .event-date { position: absolute; top: 33px; width: 100%; font-size: 14.5px; }

  .details {
    position: absolute; left: 0; top: 864px; width: 829px; height: 211px;
    background: var(--slate); color: var(--white);
  }
  .details-divider { position: absolute; left: 471px; top: 5px; width: 3px; height: 181px; background: var(--teal); }
  .details-col { position: absolute; top: 40px; font-size: 14px; line-height: 21.8px; white-space: nowrap; }
  .details-col p + p { margin-top: 21.8px; }
  .details-col.left { left: 67px; }
  .details-col.right { left: 510px; }
</style>
</head>
<body>
<main class="flyer">
  <svg class="photo-collage" viewBox="0 0 914 473" preserveAspectRatio="none">
    <defs>
      <linearGradient id="field-coach" x1="0" y1="0" x2="0" y2="1">
        <stop offset="0" stop-color="#7d8a86"/><stop offset="0.5" stop-color="#a7453f"/><stop offset="1" stop-color="#5f8a3c"/>
      </linearGradient>
      <linearGradient id="field-talk" x1="0" y1="0" x2="1" y2="1">
        <stop offset="0" stop-color="#6f9a55"/><stop offset="0.5" stop-color="#b33a33"/><stop offset="1" stop-color="#4e7f36"/>
      </linearGradient>
      <linearGradient id="field-swing" x1="0" y1="0" x2="0" y2="1">
        <stop offset="0" stop-color="#5f8c3e"/><stop offset="0.45" stop-color="#d24a2e"/><stop offset="0.8" stop-color="#b9b4b8"/><stop offset="1" stop-color="#b48864"/>
      </linearGradient>
    </defs>
    <rect width="914" height="473" fill="#ffffff"/>
    <g role="img" aria-label="Photo: coach talking with young players in pinstripe uniforms on the field">
      <polygon points="0,0 606,0 548,232 0,232" fill="url(#field-coach)"/>
    </g>
    <g role="img" aria-label="Photo: coach giving one-on-one instruction to a helmeted batter">
      <polygon points="0,242 545,242 487,473 0,473" fill="url(#field-talk)"/>
    </g>
    <g role="img" aria-label="Photo: batter in red jersey swinging at home plate">
      <polygon points="615,0 914,0 914,473 497,473" fill="url(#field-swing)"/>
    </g>
  </svg>

  <div class="brand-mark"><span class="dot"></span><span>K7T</span></div>

  <section class="mission">
    <svg viewBox="0 0 829 99" width="829" height="99">
      <rect width="829" height="99" fill="var(--slate)"/>
      <polygon points="97,0 756,0 729,99 70,99" fill="var(--white)"/>
      <polygon points="103,0 750,0 723,99 76,99" fill="var(--teal)"/>
    </svg>
    <div class="mission-text">
      <p class="mission-label">OUR MISSION</p>
      <p class="mission-line">TO TRAIN, INSTRUCT, MOTIVATE &amp; EMPOWER</p>
      <p class="mission-tagline">THE ATHLETE INSIDE YOU</p>
    </div>
  </section>

  <p class="statement">We do elite level training with youth to professional athletes &amp;<br>brand awareness is our number one concern right now</p>

  <div class="program clinics">
    <div class="program-badge">CLINICS</div>
    <p class="program-note">(1-Day Event to attract<br>50+ Athletes)</p>
  </div>
  <div class="program camps">
    <div class="program-badge">CAMPS</div>
    <p class="program-note">(2-4 Day Events looking<br>to attract 100+)</p>
  </div>
  <div class="program academies">
    <div class="program-badge small">ACADEMIES</div>
    <p class="program-note">(More intimate and skill<br>specific. lasts 6-8 weeks.<br>10-20 athletes)</p>
  </div>

  <section class="event-bar">
    <h1 class="event-title">K7T BASEBALL CLINIC</h1>
    <p class="event-date">Date: November 11th, 2017</p>
  </section>

  <section class="details">
    <div class="details-col left">
      <p>AGES:<br>PREP: (5th to 8th Grade).<br>ELITE (9th-12th Grade)</p>
      <p>Registration:<br>8:00am - 9:00 am / 11:00 am - Noon</p>
    </div>
    <div class="details-divider"></div>
    <div class="details-col right">
      <p>Times:<br>PREP: 9:00am - 11:00 am<br>ELITE: Noon - 2pm</p>
      <p>Investment: $199<br>Current Members: $99</p>
    </div>
  </section>
</main>
</body>
</html>
```